Packaging designed for both the bar and the box for retail and online sales

The name of the product is Plim Crumb. We manufacture a consumer package good product that's a healthy edible cookie dough bar. The product look, feels and tastes like cookie dough. It's sold in the refrigerator section of retail stores next to cookie dough and sunny slab. The product is Gluten Free, Diary Free and include B-12, Biotin and Collagen. The ingredients are natural. When design this think about who eat cookie dough and how to engage the buyer in purchasing the product.

We needs design packaging designed for both the bar and the box. I have attached the die lines for both products.

Target Market(s)

Our customer is 16-45. Primarily female but really anyone. Middle to upper income. Interest include healthy life style and yoga. Like to eat something sweet but not feel guilty.

Colors

Designer to choose colors to be used in the design.

Requirements
Must have
• Must be clean, warm, inviting. Brand designs I really like are Sunny Slab.
Should not have
• Should not have a photo of food

```html
<!DOCTYPE html>
<html lang="en">
<head>
<meta charset="utf-8">
<title>Plim Crumb Protein Bar Wrapper</title>
<link rel="stylesheet" href="https://fonts.googleapis.com/css2?family=Anton&family=Bebas+Neue&display=swap">
<style>
  :root {
    --bg: #d9dadb;
    --wrapper: #ffffff;
    --teal: #23697a;
    --teal-light: #3cc4c8;
    --ink: #111111;
    --paper: #ffffff;
  }
  html, body {
    margin: 0;
    padding: 0;
    width: 1200px;
    height: 803px;
    overflow: hidden;
    background: var(--bg);
  }
  .canvas {
    position: relative;
    width: 1200px;
    height: 803px;
    background: linear-gradient(180deg, #e4e5e6 0%, #cfd0d1 100%);
  }
  .wrapper {
    position: absolute;
    left: 50px;
    top: 226px;
    width: 1100px;
    height: 350px;
    background: var(--wrapper);
    overflow: hidden;
    box-shadow: 0 10px 24px rgba(0,0,0,0.12);
  }
  .chevrons {
    position: absolute;
    left: 0;
    top: 0;
    width: 320px;
    height: 350px;
  }
  .brand-name {
    position: absolute;
    left: 245px;
    top: 28px;
    width: 620px;
    margin: 0;
    text-align: center;
    font-family: "Anton", sans-serif;
    font-weight: 400;
    font-size: 102px;
    line-height: 1;
    letter-spacing: 1px;
    color: var(--ink);
  }
  .banner {
    position: absolute;
    left: 280px;
    top: 138px;
    width: 550px;
    height: 136px;
  }
  .banner svg {
    position: absolute;
    inset: 0;
  }
  .banner-title {
    position: absolute;
    left: 0;
    right: 0;
    top: 14px;
    margin: 0;
    text-align: center;
    font-family: "Bebas Neue", sans-serif;
    font-weight: 400;
    font-size: 92px;
    line-height: 1;
    letter-spacing: 1px;
    color: var(--paper);
  }
  .banner-tagline {
    position: absolute;
    left: 45px;
    top: 96px;
    width: 442px;
    height: 32px;
    box-sizing: border-box;
    border: 2px solid var(--paper);
    text-align: center;
    font-family: "Bebas Neue", sans-serif;
    font-size: 27px;
    line-height: 30px;
    letter-spacing: 1.5px;
    color: var(--paper);
  }
  .claims {
    position: absolute;
    left: 430px;
    top: 288px;
    display: flex;
    gap: 18px;
  }
  .claim {
    width: 54px;
    height: 54px;
    box-sizing: border-box;
    border: 3px solid var(--ink);
    border-radius: 50%;
    display: flex;
    align-items: center;
    justify-content: center;
    text-align: center;
    font-family: "Anton", sans-serif;
    color: var(--ink);
    line-height: 0.95;
  }
  .claim-small { font-size: 12px; }
  .claim-large { font-size: 26px; }
</style>
</head>
<body>
  <main class="canvas">
    <section class="wrapper" aria-label="Plim Crumb protein bar wrapper">
      <svg class="chevrons" viewBox="0 0 320 350" aria-hidden="true">
        <g fill="none" stroke="var(--teal)" stroke-width="46" stroke-linejoin="miter">
          <polyline points="-100,-40 110,175 -100,390"/>
          <polyline points="-20,-40 190,175 -20,390"/>
          <polyline points="65,-40 275,175 65,390"/>
        </g>
      </svg>

      <h1 class="brand-name">PLIM CRUMB</h1>

      <div class="banner">
        <svg viewBox="0 0 550 136" width="550" height="136" aria-hidden="true">
          <polygon fill="var(--teal-light)" points="0,8 550,8 530,68 550,128 0,128 20,68"/>
          <polygon fill="var(--teal)" points="12,0 538,0 520,68 538,136 12,136 30,68"/>
        </svg>
        <h2 class="banner-title">PROTEIN BAR</h2>
        <p class="banner-tagline" style="margin:0">HEALTHY EDIBLE COOKIE DOUGH BAR</p>
      </div>

      <div class="claims">
        <div class="claim claim-small">B-12<br>BIOTIN</div>
        <div class="claim claim-large">DF</div>
        <div class="claim claim-small">GLUTEN<br>FREE</div>
      </div>
    </section>
  </main>
</body>
</html>
```